Business cards - BRENT Roofing & Siding

We need simple business cards made up for our Roofing & Siding business based in Calgary Alberta.
The logo on one side of the card and potentially our slogan "Built with trust, verified by time".
The other side could have:
-A small logo
-Rep name:
-Rep cell phone:
-Rep email:
-Office phone: 403-684-2093
-Website: PrairieShingleWorks.com

We would like to incorporate the colours from our logo, especially the lite blue on the jpeg file. I have attached the ai file and jpeg file. We like the colours better on the jpeg file.

I do not require a money back guarantee

```html
<!DOCTYPE html>
<html lang="en">
<head>
<meta charset="utf-8">
<title>BRENT Roofing &amp; Siding – Business Cards</title>
<link rel="stylesheet" href="https://fonts.googleapis.com/css2?family=Montserrat:wght@400;500;600;700&display=swap">
<style>
  :root {
    --brand-blue: #0a66b7;
    --accent-blue: #1a8cf0;
    --ink: #222427;
    --muted: #5d6168;
    --card-white: #ffffff;
    --backdrop: #2b2c2f;
  }
  * { box-sizing: border-box; margin: 0; padding: 0; }
  html, body {
    width: 1200px; height: 852px; overflow: hidden;
    background: var(--backdrop);
    font-family: "Montserrat", sans-serif;
  }
  .sheet {
    width: 1200px; height: 852px;
    display: flex; flex-direction: column;
    align-items: center; justify-content: center; gap: 40px;
  }
  .card {
    position: relative;
    width: 620px; height: 354px;
    border-radius: 22px;
    overflow: hidden;
  }
  .card--front {
    background: var(--brand-blue);
    display: flex; align-items: center; justify-content: center;
  }
  .front-brand {
    color: var(--card-white);
    font-weight: 600;
    font-size: 34px;
    letter-spacing: 0.12em;
    text-align: center;
  }
  .card--back { background: var(--card-white); }
  .back-brand {
    position: absolute; left: 44px; top: 70px;
    color: var(--ink);
    font-weight: 600;
    font-size: 24px;
    letter-spacing: 0.1em;
  }
  .divider {
    position: absolute; left: 44px; right: 36px; top: 160px;
    height: 1.5px; background: var(--accent-blue);
  }
  .rep {
    position: absolute; right: 44px; top: 104px;
    text-align: right;
  }
  .rep-name {
    color: var(--accent-blue);
    font-weight: 700; font-size: 24px; letter-spacing: 0.01em;
  }
  .rep-title {
    color: var(--muted);
    font-weight: 400; font-size: 15px; letter-spacing: 0.06em;
    margin-top: 2px;
  }
  .tab {
    position: absolute; right: -10px; top: 96px;
    width: 22px; height: 40px; border-radius: 10px;
    background: var(--accent-blue);
  }
  .contacts {
    position: absolute; left: 44px; bottom: 34px;
    list-style: none;
    display: flex; flex-direction: column; gap: 6px;
  }
  .contact {
    display: flex; align-items: center; gap: 10px;
    color: var(--ink); font-size: 16px; font-weight: 400;
  }
  .contact svg { width: 14px; height: 14px; flex: none; }
</style>
</head>
<body>
  <main class="sheet">
    <section class="card card--front" aria-label="Card front">
      <p class="front-brand">BRENT Roofing &amp; Siding</p>
    </section>

    <section class="card card--back" aria-label="Card back">
      <p class="back-brand">BRENT Roofing &amp; Siding</p>
      <div class="tab"></div>
      <div class="rep">
        <p class="rep-name">DANIEL REEVES</p>
        <p class="rep-title">DIRECTOR</p>
      </div>
      <div class="divider"></div>
      <ul class="contacts">
        <li class="contact">
          <svg viewBox="0 0 16 16" aria-hidden="true"><path d="M3.5 1.5l3 3-1.6 1.8a9 9 0 0 0 4.8 4.8l1.8-1.6 3 3-2 2C6.8 14 2 9.2 1.5 3.5z" fill="var(--accent-blue)"/></svg>
          403-684-2093
        </li>
        <li class="contact">
          <svg viewBox="0 0 16 16" aria-hidden="true"><rect x="4" y="1" width="8" height="14" rx="1.5" fill="none" stroke="var(--accent-blue)" stroke-width="1.6"/><circle cx="8" cy="12.3" r="0.9" fill="var(--accent-blue)"/></svg>
          905-318-4470
        </li>
        <li class="contact">
          <svg viewBox="0 0 16 16" aria-hidden="true"><rect x="1" y="3.5" width="14" height="9" rx="1" fill="none" stroke="var(--accent-blue)" stroke-width="1.5"/><path d="M1.5 4l6.5 5 6.5-5" fill="none" stroke="var(--accent-blue)" stroke-width="1.5"/></svg>
          brentroof@northmail.net
        </li>
        <li class="contact">
          <svg viewBox="0 0 16 16" aria-hidden="true"><g fill="none" stroke="var(--accent-blue)" stroke-width="1.3"><circle cx="8" cy="8" r="6.5"/><ellipse cx="8" cy="8" rx="3" ry="6.5"/><path d="M1.5 8h13M2.5 4.8h11M2.5 11.2h11"/></g></svg>
          prairieshingleworks.com
        </li>
      </ul>
    </section>
  </main>
</body>
</html>
```